Veltrova Website

I would like to have a revised web site for Veltrova. Veltrova is two companies - Veltrova Insurance Company and Veltrova Re Intermediaries. The logos are set, the site content is set, but the flow and look of the web site is clunky.

We do need a landing page that allows someone to choose either company. The one we have is very basic.

Current photos are not required, just ones we used.

www.veltrova-example.com is the site.

Target Market(s)

Business professionals (insurance)

Industry/Entity Type

Insurance

Requirements
Must have
• Veltrova Insurance Company
• Veltrova Re Intermediaries
• Current logos

```html
<!DOCTYPE html>
<html lang="en">
<head>
<meta charset="utf-8">
<title>Veltrova Re Intermediaries</title>
<link rel="stylesheet" href="https://fonts.googleapis.com/css2?family=PT+Sans:ital,wght@0,400;0,700;1,400&family=Oswald:wght@500&display=swap">
<style>
:root{
  --red:#e1262c;
  --ink:#2b2b2b;
  --muted:#555;
  --soft:#f1f2f3;
  --footer:#0d0d0d;
  --white:#fff;
}
*{box-sizing:border-box;margin:0;padding:0}
html,body{width:1065px;height:1200px;overflow:hidden;background:var(--white)}
body{position:relative;font-family:"PT Sans",sans-serif;color:var(--ink)}
.top-rule{position:absolute;left:0;top:0;width:100%;height:6px;background:var(--red)}
.brand{position:absolute;left:78px;top:82px;display:flex;align-items:center;gap:10px}
.brand-mark{width:22px;height:22px;background:var(--red)}
.brand-name{font-size:28px;font-weight:400;color:#1d2433;letter-spacing:1px}
.search{position:absolute;left:786px;top:48px;width:201px;height:30px;border:1px solid #c9c9c9;border-radius:3px;padding:0 10px;display:flex;align-items:center;justify-content:space-between;font-size:12px;font-style:italic;color:#999}
.main-nav{position:absolute;right:78px;top:110px;display:flex;font-size:16px}
.main-nav a{color:#222;text-decoration:none;padding:0 21px;border-left:1px dotted #bbb;line-height:20px}
.main-nav a:first-child{border-left:0}
.main-nav a:last-child{padding-right:0}
.main-nav a.active{color:var(--red)}
.hero{position:absolute;left:0;top:155px;width:1065px;height:388px;background:linear-gradient(100deg,#d7dcdf 0%,#aebdc6 30%,#6f7e8a 50%,#9fb7c4 70%,#c9dbe2 100%)}
.hero-caption{position:absolute;left:78px;top:191px;width:438px;height:155px;background:rgba(70,70,70,.78);padding:18px 28px;color:var(--white)}
.hero-title{font-family:"Oswald",sans-serif;font-weight:500;font-size:27px;line-height:32px;letter-spacing:.3px}
.hero-sub{font-size:20px;line-height:26px;margin-top:3px}
.hero-text{font-size:14px;line-height:22px;margin-top:7px}
.hero-dots{position:absolute;left:930px;top:365px;display:flex;gap:4px}
.hero-dots span{width:11px;height:11px;border-radius:50%;background:#e6e6e6}
.hero-dots span.on{background:#777;border:2px solid #ddd}
.services{position:absolute;left:58px;top:586px;display:flex}
.service{width:238px;text-align:center}
.service svg{width:76px;height:76px;display:block;margin:0 auto}
.service h3{color:var(--red);font-size:19px;font-weight:700;margin-top:18px}
.service p{font-size:13px;line-height:19px;color:#222;margin-top:4px}
.welcome{position:absolute;left:78px;top:820px;width:600px}
.section-title{font-size:24px;font-weight:400;color:#222}
.welcome-photo{position:absolute;left:0;top:50px;width:195px;height:188px;border-radius:5px;background:linear-gradient(180deg,#3f7ec6 0%,#8fb9e2 55%,#5d9b2f 78%,#7dbb2e 100%)}
.welcome-body{position:absolute;left:214px;top:44px;width:384px}
.welcome-lead{font-size:15px;line-height:23px;color:#444}
.welcome-text{font-size:12.5px;line-height:20.5px;color:#555;margin-top:8px}
.testimonials{position:absolute;left:725px;top:820px;width:262px}
.quote{position:relative;margin-top:24px;margin-left:2px;width:259px;height:112px;background:var(--soft);padding:12px 18px;font-size:12px;font-style:italic;line-height:21px;color:#555}
.quote::after{content:"";position:absolute;left:178px;bottom:-26px;border-top:26px solid var(--soft);border-left:34px solid transparent}
.author{position:relative;margin-top:15px;height:67px}
.avatar{position:absolute;left:9px;top:0;width:75px;height:67px;background:linear-gradient(180deg,#e9e9e9,#c9ccd0 60%,#2a2d33 100%)}
.author-role{position:absolute;left:114px;top:16px;font-size:12px;font-weight:700;color:#333}
.author-name{position:absolute;left:114px;top:44px;font-size:12px;font-weight:700;color:#333;display:flex;align-items:center;gap:8px}
.site-footer{position:absolute;left:0;top:1108px;width:1065px;height:92px;background:var(--footer);color:var(--white)}
.footer-links{position:absolute;left:78px;top:24px;font-size:12px}
.copyright{position:absolute;left:78px;top:54px;font-size:12px}
.social{position:absolute;left:826px;top:30px;display:flex;gap:12px}
.social span{width:32px;height:32px;background:var(--red)}
</style>
</head>
<body>
<div class="top-rule"></div>

<header>
  <div class="brand"><span class="brand-mark"></span><span class="brand-name">VELTROVA RE</span></div>
  <div class="search"><span>Search..</span>
    <svg width="12" height="12" viewBox="0 0 12 12"><circle cx="5" cy="5" r="3.8" fill="none" stroke="#999" stroke-width="1.6"/><line x1="8" y1="8" x2="11" y2="11" stroke="#999" stroke-width="1.8"/></svg>
  </div>
  <nav class="main-nav">
    <a class="active" href="#">HOME</a><a href="#">SERVICES</a><a href="#">ABOUT US</a><a href="#">CONTACT</a>
  </nav>
</header>

<section class="hero" role="img" aria-label="Blurred photo of business professionals shaking hands in a bright office">
  <div class="hero-caption">
    <div class="hero-title">THE DAYS OF BUYING EXPENSIVE</div>
    <div class="hero-sub">DON'T BUY ANYMORE IN-STORE SERVICE</div>
    <p class="hero-text">Jerta baditaut onsequser untur magni dolores eoquie volup tate msequi nesciunt. Voluptatem accusantium dolorem.</p>
  </div>
  <div class="hero-dots"><span class="on"></span><span></span><span></span><span></span></div>
</section>

<section class="services">
  <div class="service">
    <svg viewBox="0 0 76 76" fill="none" stroke="var(--red)" stroke-width="3.5">
      <g transform="translate(38 38)">
        <path d="M-6-34h12l2 9 7 3 8-5 8 8-5 8 3 7 9 2v12l-9 2-3 7 5 8-8 8-8-5-7 3-2 9h-12l-2-9-7-3-8 5-8-8 5-8-3-7-9-2v-12l9-2 3-7-5-8 8-8 8 5 7-3z" stroke-linejoin="round"/>
        <circle r="14"/><circle r="7"/>
      </g>
    </svg>
    <h3>Reinsurance Services</h3>
    <p>Lorem ipsum dolor sit amet<br>ing elit.Morbi ut elipsum tristiqu<br>Pellentesque habitant morb</p>
  </div>
  <div class="service">
    <svg viewBox="0 0 76 76" fill="none" stroke="var(--red)" stroke-width="3.5">
      <path d="M58 38V20L44 5H8v68h34" stroke-linejoin="round"/>
      <path d="M44 5v15h14"/>
      <path d="M17 25h20M17 35h32M17 45h22M17 55h16"/>
      <circle cx="56" cy="56" r="15" fill="var(--red)" stroke="none"/>
      <circle cx="56" cy="48" r="2.4" fill="#fff" stroke="none"/>
      <rect x="54" y="53" width="4" height="12" fill="#fff" stroke="none"/>
    </svg>
    <h3>Brokerage Services</h3>
    <p>Lorem ipsum dolor sit amet<br>ing elit.Morbi ut elipsum tristiqu<br>Pellentesque habitant morb</p>
  </div>
  <div class="service">
    <svg viewBox="0 0 76 76" fill="none" stroke="var(--red)" stroke-width="3.5" stroke-linejoin="round">
      <path d="M74 3L3 45l22 8 6 20 12-13 17 9z"/>
      <path d="M74 3L25 53M74 3L31 73"/>
    </svg>
    <h3>Claims TPA</h3>
    <p>Lorem ipsum dolor sit amet<br>ing elit.Morbi ut elipsum tristiqu<br>Pellentesque habitant morb</p>
  </div>
  <div class="service">
    <svg viewBox="0 0 76 76" fill="var(--red)">
      <path d="M38 2c12 0 22 9 22 21 0 11-8 16-10 29H26C24 39 16 34 16 23 16 11 26 2 38 2z"/>
      <rect x="27" y="56" width="22" height="4" rx="2"/>
      <rect x="27" y="63" width="22" height="4" rx="2"/>
      <rect x="30" y="70" width="16" height="4" rx="2"/>
    </svg>
    <h3>Product Analysis</h3>
    <p>Lorem ipsum dolor sit amet<br>ing elit.Morbi ut elipsum tristiqu<br>Pellentesque habitant morb</p>
  </div>
</section>

<section class="welcome">
  <h2 class="section-title">Welcome to our website</h2>
  <div class="welcome-photo" role="img" aria-label="Photo of modern glass office towers above a green lawn"></div>
  <div class="welcome-body">
    <p class="welcome-lead">Ut wisi enim ad minim veniam, quis nostrud exerci tation ulli amcorper suscipit lobortis nisl ut aliquip exea.</p>
    <p class="welcome-text">Incididunt ut labore et dolore magna aliqua. Ut enim ad minim veniam, quis nostrud exercitation ullamcolaboris nisi ut aliquip ex ea commodo consequat. Duis tefd aute iruredolor inreprehenderit in voluptate velit esse cillum.Dolore magna aliqua. Ut enim ad minim veniam, Quisnostru dexercitation ullamco laboris nisi ut aliquip. Ut enim ad minim veniam, quis nostrud exercitation ullamco laboris. Claritas est etiam processus dynamicus, qui sequitur mutationem.</p>
  </div>
</section>

<aside class="testimonials">
  <h2 class="section-title">Testimonials</h2>
  <blockquote class="quote">Fusce feugiat malesuada odio. Morbi nunc do gravida at, cursus nec, luctus a, lorem. Maecn as tristique orci acd sem. Lorem ipsum dolorsi t amet, consectetur adipisicing elit</blockquote>
  <div class="author">
    <div class="avatar" role="img" aria-label="Portrait photo of the client giving the testimonial"></div>
    <div class="author-role">Maecenintty interu coquat</div>
    <div class="author-name">
      <svg width="13" height="13" viewBox="0 0 13 13" fill="#555"><circle cx="6.5" cy="3.5" r="3.3"/><path d="M0 13c0-4 3-6 6.5-6S13 9 13 13z"/></svg>
      Dana Merrow's
    </div>
  </div>
</aside>

<footer class="site-footer">
  <div class="footer-links">Home | Services | About us | Contact</div>
  <div class="copyright">Copyrights 2013. All Rights Reserved.</div>
  <div class="social"><span></span><span></span><span></span><span></span></div>
</footer>
</body>
</html>
```